Design a refer a friend Flyer (French & English)
Flyer Title:
Main Title: "Refer a Friend & Receive a Free Electric Toothbrush!"
Bold and clear, centered at the top.
Use a clean and modern font.
Color: White text on a vivid green background for maximum contrast and readability.
Visual Focus:
Toothbrush Image: Place a high-quality image of the Dentiva Max 300 Electric Toothbrush in the center of the flyer.
Include a small price tag with “Value of $50” near the toothbrush to highlight the reward.
Simple Message:
Text: "Refer a friend to Centre Dentaire Lac-Ombré. When they book and attend their appointment, you get a free electric toothbrush, and they receive a special gift!"
Straightforward and easy to understand.
Placed below the image of the toothbrush.
Referral Process:
3 Easy Steps:
Refer a Friend
They Book and Come to Their Appointment
Receive Your Free Electric Toothbrush
Use simple, minimal icons to visually represent each step.
Keep the steps aligned horizontally or vertically for clarity.
Call to Action:
Text: "Start Referring Today!"
Place it in a button-like design in the vivid green color with bold, white text to make it stand out.
Contact Information:
Details:
Logo of Centre Dentaire Lac-Ombré.
Address: "42 Rue Valmonde Ouest, Suite 310".
Phone Number and Website: Positioned at the bottom for easy reference.
Color Scheme:
Use a vivid green background for the entire flyer, with white accents for text and icons to maintain a fresh, clean look.
Minimal clutter, focusing on clarity and the key elements: the toothbrush, the call to action, and contact information.
Clinic : www.cdlacombre.example
Attached is the brandbook, logo and inspo I made with AI.
French text will be provided.
Thank you,
Tarin

```html
<!DOCTYPE html>
<html lang="en">
<head>
<meta charset="utf-8">
<title>Refer a Friend – Clinique Dentaire Lac-Ombré</title>
<link href="https://fonts.googleapis.com/css2?family=Montserrat:wght@600;700;800;900&display=swap" rel="stylesheet">
<style>
  :root {
    --green: #0f9b5b;
    --green-light: #53ba6b;
    --white: #ffffff;
    --black: #111111;
    --stage: #e4e4e4;
    --brush-dark: #1d1d1d;
    --brush-light: #f2f2f2;
  }
  * { margin: 0; padding: 0; box-sizing: border-box; }
  html, body { width: 1200px; height: 1200px; overflow: hidden; }
  body {
    background: var(--stage);
    font-family: "Montserrat", sans-serif;
    position: relative;
  }
  .flyer {
    position: absolute;
    left: 150px; top: 18px;
    width: 900px; height: 1164px;
    background: var(--green);
    overflow: hidden;
    color: var(--white);
  }
  .title-band {
    position: absolute;
    left: 24px; top: 22px;
    width: 852px; height: 150px;
    background: var(--green-light);
    border-radius: 0 40px 40px 40px;
    display: flex; align-items: center; justify-content: center;
  }
  .title-main {
    font-weight: 900; font-size: 92px; letter-spacing: 1px;
    line-height: 1; white-space: nowrap;
  }
  .title-sub {
    position: absolute; left: 0; width: 100%; top: 186px;
    text-align: center; font-weight: 900; font-size: 66px;
    color: var(--black); line-height: 1; white-space: nowrap;
  }
  .title-sub-2 {
    position: absolute; left: 0; width: 100%; top: 262px;
    text-align: center; font-weight: 900; font-size: 54px; line-height: 1; white-space: nowrap;
  }
  .toothbrush {
    position: absolute; left: 395px; top: 335px;
    width: 130px; height: 770px;
  }
  .brush-arrows {
    position: absolute; left: 330px; top: 350px;
    width: 260px; height: 50px;
  }
  .steps {
    position: absolute; left: 50px; top: 640px; width: 340px;
    text-align: center;
  }
  .steps__lead { font-weight: 900; font-size: 34px; margin-bottom: 20px; white-space: nowrap; }
  .steps__item { font-weight: 800; font-size: 23px; line-height: 1.25; margin-bottom: 24px; }
  .value {
    position: absolute; left: 40px; top: 860px; width: 360px;
    text-align: center; font-weight: 900; line-height: 1;
  }
  .value__label { font-size: 62px; white-space: nowrap; }
  .value__amount { font-size: 176px; letter-spacing: -4px; margin-top: 4px; }
  .message {
    position: absolute; left: 560px; top: 600px; width: 315px;
    font-weight: 700; font-size: 20px; line-height: 1.85;
  }
  .cta {
    position: absolute; left: 560px; top: 842px; width: 310px; height: 96px;
    background: var(--white); color: var(--black);
    border: 4px solid var(--black); border-radius: 26px;
    display: flex; align-items: center; justify-content: center;
    text-align: center; font-weight: 900; font-size: 28px; line-height: 1.1;
  }
  .clinic {
    position: absolute; left: 565px; top: 962px; width: 320px;
  }
  .clinic__name {
    font-weight: 700; font-size: 30px; line-height: 1;
    white-space: nowrap;
    display: flex; align-items: center; gap: 12px;
  }
  .clinic__dot {
    flex: none; width: 18px; height: 18px; border-radius: 50%; background: var(--white);
  }
  .clinic__branch {
    margin-top: 6px;
    font-weight: 700; font-size: 14px; line-height: 1;
  }
  .contact {
    position: absolute; left: 567px; top: 1030px; width: 325px;
    font-style: normal;
    font-weight: 800; font-size: 16px; line-height: 1.5;
  }
  .contact__row { margin-bottom: 4px; white-space: nowrap; }
</style>
</head>
<body>
  <main class="flyer">
    <div class="title-band"><h1 class="title-main">REFER A FRIEND</h1></div>
    <p class="title-sub">&amp; RECEIVE A FREE</p>
    <p class="title-sub-2">ELECTRIC TOOTHBRUSH!</p>

    <svg class="brush-arrows" viewBox="0 0 260 50" aria-hidden="true">
      <path d="M70 30 Q50 10 20 26" fill="none" stroke="#fff" stroke-width="5" stroke-linecap="round"/>
      <path d="M20 26 l12 -12 M20 26 l16 4" stroke="#fff" stroke-width="5" stroke-linecap="round"/>
      <path d="M190 30 Q210 10 240 26" fill="none" stroke="#fff" stroke-width="5" stroke-linecap="round"/>
      <path d="M240 26 l-12 -12 M240 26 l-16 4" stroke="#fff" stroke-width="5" stroke-linecap="round"/>
    </svg>

    <svg class="toothbrush" viewBox="0 0 130 770" role="img" aria-label="Dentiva Max 300 electric toothbrush product photo">
      <defs>
        <linearGradient id="brushBody" x1="0" x2="0" y1="0" y2="1">
          <stop offset="0" stop-color="#f2f2f2"/>
          <stop offset="0.38" stop-color="#f2f2f2"/>
          <stop offset="0.42" stop-color="#1d1d1d"/>
          <stop offset="0.86" stop-color="#1d1d1d"/>
          <stop offset="0.88" stop-color="#f2f2f2"/>
          <stop offset="1" stop-color="#f2f2f2"/>
        </linearGradient>
      </defs>
      <rect x="0" y="0" width="130" height="770" rx="55" fill="url(#brushBody)"/>
    </svg>

    <section class="steps">
      <p class="steps__lead">REFER A FRIEND</p>
      <p class="steps__item">They Book and Come<br>to Their Appointment</p>
      <p class="steps__item">Receive Your Free<br>Electric Toothbrush</p>
    </section>

    <div class="value">
      <p class="value__label">VALUE OF</p>
      <p class="value__amount">$50</p>
    </div>

    <p class="message">Refer a friend to Centre Dentaire Lac-Ombré. When they book and attend their appointment, you get a free electric toothbrush, and they receive a special gift!</p>

    <div class="cta">START REFERRING<br>TODAY!</div>

    <div class="clinic">
      <p class="clinic__name">Clinique Dentaire <span class="clinic__dot"></span></p>
      <p class="clinic__branch">Lac-Ombré</p>
    </div>

    <address class="contact">
      <p class="contact__row">Address:<br>42 Rue Valmonde Ouest, Suite 310.</p>
      <p class="contact__row">Phone: 514-555-0182</p>
      <p class="contact__row">Clinic : www.cdlacombre.example</p>
    </address>
  </main>
</body>
</html>
```